Harborline Renewal Business Card Design

Professional and clean design. The design colors should flow with the logo. Two-sided card with the website on the back which is:

www.HarborlineRenewal.example.

"Specializing in Water Damage Restoration"

On the front I need the name, email, phone, and logo.

Name: Darnell Quisby
Email: Darnell@HarborlineRenewal.example
Phone: 555-318-2046 for now

I only have the Preview and Thumbnail right now but should have the source files uploaded within a day or two.

Target Market(s)

Flood victims, home owners with water damage from busted pipes etc...

Industry/Entity Type

Business

Contact Information for Business Card

Name: Darnell Quisby

Font styles to use
Serif
Sans Serif

Requirements
Must have
• Business Card Details Info

```html
<!DOCTYPE html>
<html lang="en">
<head>
<meta charset="utf-8">
<title>Harborline Renewal Business Card</title>
<link rel="stylesheet" href="https://fonts.googleapis.com/css2?family=Cinzel:wght@400;600;700&family=Open+Sans:wght@400;600&display=swap">
<style>
  :root {
    --page: #eceef0;
    --brand-blue: #2b96d3;
    --deep-blue: #2087c8;
    --light-blue: #5bc0ec;
    --card-white: #ffffff;
    --ink: #3a3a3a;
    --muted: #555b60;
  }
  * { box-sizing: border-box; margin: 0; padding: 0; }
  html, body { width: 1200px; height: 1120px; overflow: hidden; }
  body { background: var(--page); position: relative; font-family: "Open Sans", sans-serif; }

  .card {
    position: absolute;
    width: 760px;
    height: 430px;
    box-shadow: 0 6px 18px rgba(0,0,0,0.15);
    overflow: hidden;
  }

  /* Back side */
  .card-back { left: 140px; top: 50px; background: var(--brand-blue); color: var(--card-white); text-align: center; }
  .back-mark { width: 170px; height: 170px; border-radius: 50%; background: var(--card-white); margin: 50px auto 0; }
  .back-name { font-family: "Cinzel", serif; font-weight: 600; font-size: 30px; letter-spacing: 2px; margin-top: 22px; }
  .back-tagline { font-family: "Cinzel", serif; font-weight: 400; font-size: 22px; letter-spacing: 1px; margin-top: 40px; }

  /* Front side */
  .card-front { left: 300px; top: 620px; background: var(--card-white); }
  .brand { position: absolute; right: 40px; top: 30px; display: flex; flex-direction: column; align-items: center; }
  .brand-mark { width: 70px; height: 70px; border-radius: 50%; background: var(--brand-blue); }
  .brand-name { font-family: "Cinzel", serif; font-weight: 700; font-size: 32px; color: var(--brand-blue); margin-top: 8px; letter-spacing: 1px; line-height: 1.1; }

  .rules { position: absolute; left: 0; top: 0; }

  .person { position: absolute; left: 40px; top: 208px; }
  .person-name { font-family: "Cinzel", serif; font-weight: 600; font-size: 26px; line-height: 34px; color: var(--deep-blue); letter-spacing: 1px; }
  .person-title { font-family: "Cinzel", serif; font-weight: 400; font-size: 22px; line-height: 30px; color: var(--ink); letter-spacing: 2px; }

  .contact { position: absolute; left: 40px; top: 298px; list-style: none; font-size: 17px; color: var(--muted); }
  .contact li { display: flex; align-items: center; gap: 10px; height: 34px; }
  .contact svg { width: 16px; height: 16px; fill: var(--deep-blue); flex: none; }

  .website { position: absolute; right: 20px; top: 356px; font-size: 16px; line-height: 20px; color: var(--card-white); white-space: nowrap; }
</style>
</head>
<body>

<section class="card card-back" aria-label="Card back">
  <div class="back-mark"></div>
  <p class="back-name">Harborline Renewal</p>
  <p class="back-tagline">Specializing in Water Damage Restoration</p>
</section>

<section class="card card-front" aria-label="Card front">
  <div class="brand">
    <div class="brand-mark"></div>
    <p class="brand-name">Harborline Renewal</p>
  </div>

  <svg class="rules" width="760" height="430" viewBox="0 0 760 430" aria-hidden="true">
    <line x1="150" y1="268" x2="760" y2="208" stroke="var(--light-blue)" stroke-width="2"/>
    <polygon points="0,384 448,384 440,396 0,396" fill="var(--light-blue)"/>
    <polygon points="0,404 440,404 472,344 760,344 760,430 0,430" fill="var(--deep-blue)"/>
  </svg>

  <div class="person">
    <p class="person-name">Darnell Quisby</p>
    <p class="person-title">Title</p>
  </div>

  <ul class="contact">
    <li>
      <svg viewBox="0 0 24 24" aria-hidden="true"><path d="M6.6 10.8a15 15 0 0 0 6.6 6.6l2.2-2.2c.3-.3.7-.4 1-.2 1.1.4 2.3.6 3.6.6.6 0 1 .4 1 1V20c0 .6-.4 1-1 1A17 17 0 0 1 3 4c0-.6.4-1 1-1h3.5c.6 0 1 .4 1 1 0 1.2.2 2.4.6 3.6.1.3 0 .7-.2 1z"/></svg>
      555-318-2046
    </li>
    <li>
      <svg viewBox="0 0 24 24" aria-hidden="true"><path d="M3 5h18v14H3z M3 5l9 7 9-7" fill="none" stroke="var(--deep-blue)" stroke-width="2.4"/></svg>
      Darnell@HarborlineRenewal.example
    </li>
  </ul>

  <p class="website">www.HarborlineRenewal.example</p>
</section>

</body>
</html>
```